Cedar-Rock Harvest Chapel WL- Theme for 2022

We, Cedar-Rock Harvest Chapel of Willow Landing, need a design for a 4' x 6' banner that will be placed on two walls in the main sanctuary. The banner is to communicate/advertise the church's theme for 2022, "He Will Make All Things New: A New You - 2022" Revelations 21:5. The design should include our logo and church name. Use the color purple. We have not worshipped in our church building since 2020 due to the COVID pandemic. This banner should be reflective of change, newness as we plan to re-enter the building this spring. Our congregation demographic is 95% African American, 5% Hispanic. Our home base is Tampa, Florida (USA), but we have a large social media following, primarily due to the pandemic.

Target Market(s)

Church members, Ages 1-99; male and female

Industry/Entity Type

Religious

Font styles to use
Serif

Colors
0094D4
00A9DD
6FCCEA
C7EBF8
E9F6FB
00AB8E
00BBA5
67D7C9
C6EFE9
E9F9F6
6B429C
8869AF
B7A5CE
E3DAEB
F3F0F8

Requirements
Must have
• Theme, scripture, church logo and color purple

```html
<!DOCTYPE html>
<html lang="en">
<head>
<meta charset="utf-8">
<title>Cedar-Rock Harvest Chapel WL – Theme for 2022 Banner</title>
<link rel="stylesheet" href="https://fonts.googleapis.com/css2?family=Archivo+Black&family=Barlow+Semi+Condensed:wght@700;800&family=Montserrat:wght@400;500;600&display=swap">
<style>
  :root {
    --page: #f2f2f2;
    --purple-deep: #4c0a7c;
    --purple: #5e1494;
    --purple-bright: #6c1aa8;
    --haze: #b06fd0;
    --wood-dark: #5a2a1e;
    --wood: #8a4530;
    --orange: #ff8a00;
    --white: #ffffff;
    --badge-grey: #c9c9cb;
    --cord: #1a1a1a;
  }
  * { margin: 0; padding: 0; box-sizing: border-box; }
  html, body { width: 828px; height: 1200px; overflow: hidden; background: var(--page); }
  body { position: relative; }

  .banner {
    position: absolute;
    left: 0; top: 324px;
    width: 828px; height: 552px;
    overflow: hidden;
    background: var(--purple);
    box-shadow: 0 6px 16px rgba(0,0,0,0.35);
  }
  .sanctuary-photo {
    position: absolute; inset: 0;
    background:
      linear-gradient(90deg, var(--purple-deep) 0%, var(--purple) 38%, rgba(94,20,148,0.55) 55%, rgba(94,20,148,0) 72%),
      linear-gradient(180deg, rgba(0,0,0,0) 55%, rgba(176,111,208,0.75) 68%, rgba(108,26,168,0.9) 100%),
      linear-gradient(120deg, var(--wood-dark) 30%, var(--wood) 70%, var(--wood-dark) 100%);
  }

  .theme-line {
    position: absolute; left: 37px;
    font-family: "Montserrat", sans-serif; font-weight: 500;
    font-size: 38px; line-height: 1; letter-spacing: 1px;
  }
  .theme-line--accent { top: 33px; color: var(--orange); font-weight: 400; }
  .theme-line--main { top: 67px; color: var(--white); }

  .headline {
    position: absolute; left: 35px; top: 108px;
    font-family: "Barlow Semi Condensed", sans-serif; font-weight: 800;
    font-size: 82px; line-height: 1; color: var(--orange); letter-spacing: -1px;
  }
  .year {
    position: absolute; left: 35px; top: 172px;
    font-family: "Archivo Black", sans-serif;
    font-size: 114px; line-height: 1; color: var(--white); letter-spacing: -3px;
  }
  .scripture {
    position: absolute; left: 36px; top: 282px;
    font-family: "Barlow Semi Condensed", sans-serif; font-weight: 700;
    font-size: 32px; line-height: 1; color: var(--white);
  }
  .open-band {
    position: absolute; left: 0; top: 331px;
    width: 390px; height: 52px;
    background: var(--orange);
    display: flex; align-items: center; padding-left: 37px;
    font-family: "Barlow Semi Condensed", sans-serif; font-weight: 700;
    font-size: 35px; color: var(--white); white-space: nowrap;
  }
  .church-name {
    position: absolute; left: 39px; top: 407px;
    font-family: "Barlow Semi Condensed", sans-serif; font-weight: 700;
    font-size: 22px; line-height: 26px; color: var(--white);
  }
  .website {
    position: absolute; left: 39px; top: 490px;
    font-family: "Montserrat", sans-serif; font-weight: 600;
    font-size: 17px; color: var(--white);
  }
  .social {
    position: absolute; left: 586px; top: 498px;
    display: flex; align-items: center; gap: 6px;
    font-family: "Montserrat", sans-serif; font-weight: 400;
    font-size: 15px; color: var(--white); letter-spacing: 0.5px;
  }
  .social-label { margin-right: 10px; }
  .social-square { width: 28px; height: 28px; background: var(--white); border-radius: 2px; }

  .logo-badge { position: absolute; left: 512px; top: 0; width: 216px; height: 300px; }
  .logo-badge__cord { position: absolute; left: 107px; top: 0; width: 2px; height: 86px; background: var(--cord); }
  .logo-badge__disc {
    position: absolute; left: 0; top: 84px;
    width: 216px; height: 216px; border-radius: 50%;
    background: var(--badge-grey);
    display: flex; align-items: center; justify-content: center; text-align: center;
    font-family: "Montserrat", sans-serif; font-weight: 600;
    font-size: 19px; line-height: 1.25; color: var(--purple);
    padding: 0 26px;
  }
</style>
</head>
<body>
  <main class="banner">
    <div class="sanctuary-photo" role="img" aria-label="Photo of a church sanctuary interior with wooden arches and pews, fading into purple clouds"></div>

    <p class="theme-line theme-line--accent">HE WILL MAKE</p>
    <p class="theme-line theme-line--main">ALL THINGS NEW</p>
    <h1 class="headline">A NEW YOU</h1>
    <p class="year">2022</p>
    <p class="scripture">REVELATIONS 21:5</p>

    <div class="open-band">WE ARE OPEN NOW</div>

    <p class="church-name">CEDAR-ROCK HARVEST<br>CHAPEL WL</p>
    <p class="website">www.crhcwl.org</p>

    <div class="social">
      <span class="social-label">Follow us on:</span>
      <span class="social-square" aria-hidden="true"></span>
      <span class="social-square" aria-hidden="true"></span>
    </div>

    <div class="logo-badge">
      <span class="logo-badge__cord"></span>
      <div class="logo-badge__disc">Cedar-Rock Harvest Chapel</div>
    </div>
  </main>
</body>
</html>
```